Boundless Volt Product design

We need a bottle design for our product. Boundless Volt is a Gaming Nootropic made to increase Energy, Focus, Reaction time, and Clarity of an eSport gamer. It will be 40 servings a bottle. Currently, all the ingredients haven't been finalized so after the competition is over we will have to work with the designer to also make an ingredients label for the back of it. For the flavor, we will call it tundra mist.

The attachments included:. The velvet outlaws picture as a font style I like for the logo.
The Z CHARGE REFRESH PICTURE IS WHAT WE WANT OUR DESIGN to look like something similar a clean and simple design that stands out!

Z Charge bottle is what our biggest competitors product looks like. The boundless volt picture as the current logo we are using but can be changed.

Overall the pictures are just some references for what I could possibly want the design to look like however, I'm open to your designer's ideas and concepts you think would make for a cool looking Gaming Nootropic product bottle design. I appreciate everyone working on this and look forward to seeing your designs have a great day!

Target Market(s)

Gamers between the ages of 18-30

Industry/Entity Type

Health And Wellness

Requirements
Must have
• Boundless Volt logo, state that it is for energy, focus, reaction, and clarity. state 40 serivngs. state flavor.

```html
<!DOCTYPE html>
<html lang="en">
<head>
<meta charset="utf-8">
<title>Boundless Volt – Tundra Mist Label</title>
<link href="https://fonts.googleapis.com/css2?family=Saira:wght@500;600&family=Saira+Condensed:ital,wght@0,700;1,700&family=Open+Sans:wght@500&display=swap" rel="stylesheet">
<style>
  :root {
    --backdrop: #dcdcdc;
    --label-white: #ffffff;
    --label-shade: #eef1f4;
    --royal: #2b4ea6;
    --royal-deep: #1f3f93;
    --ink-blue: #1f46a8;
    --ice: #b9d7ef;
    --teal: #4fc3cf;
    --ink: #141414;
  }
  * { box-sizing: border-box; margin: 0; padding: 0; }
  html, body { width: 1200px; height: 893px; overflow: hidden; }
  body { background: var(--backdrop); position: relative; }

  .label {
    position: absolute; left: 80px; top: 66px; width: 1040px; height: 760px;
    background: linear-gradient(180deg, var(--label-white) 55%, var(--label-shade) 100%);
    overflow: hidden;
  }
  .check-band {
    position: absolute; left: 0; top: 0; width: 100%; height: 100px;
    background: linear-gradient(180deg, var(--ice) 0%, #d6e8f6 100%);
    opacity: .85;
  }
  .servings-tab {
    position: absolute; left: 830px; top: 0; width: 84px; height: 290px;
    background: var(--royal); border-radius: 0 0 18px 18px;
    color: #fff; text-align: center;
    display: flex; flex-direction: column; justify-content: flex-end; padding-bottom: 22px;
  }
  .servings-count { font-family: "Saira Condensed", sans-serif; font-weight: 700; font-size: 58px; line-height: 1; }
  .servings-word { font-family: "Saira Condensed", sans-serif; font-weight: 700; font-size: 21px; line-height: 1.2; }

  .brand {
    position: absolute; left: 190px; top: 170px; width: 580px;
    display: flex; align-items: center; gap: 18px;
  }
  .brand-square { width: 34px; height: 34px; background: var(--teal); flex: none; }
  .brand-name {
    font-family: "Saira", sans-serif; font-weight: 500; font-size: 64px;
    color: var(--ink); letter-spacing: 1px; white-space: nowrap;
  }
  .audience {
    position: absolute; left: 215px; top: 318px;
    font-family: "Saira Condensed", sans-serif; font-style: italic; font-weight: 700;
    font-size: 46px; letter-spacing: 5px; color: var(--ink-blue);
  }

  .bottom-band { position: absolute; left: 0; top: 440px; width: 1040px; height: 320px; }

  .stat { position: absolute; top: 462px; width: 70px; text-align: center; color: #fff; }
  .stat-zero { font-family: "Saira Condensed", sans-serif; font-style: italic; font-weight: 700; font-size: 50px; line-height: 1; }
  .stat-name { font-family: "Saira Condensed", sans-serif; font-style: italic; font-weight: 700; font-size: 13px; letter-spacing: .5px; }

  .flavor {
    position: absolute; left: 610px; top: 466px;
    font-family: "Saira Condensed", sans-serif; font-style: italic; font-weight: 700;
    font-size: 50px; letter-spacing: 3px; color: #fff;
  }
  .benefits {
    position: absolute; left: 0; width: 100%; top: 590px; text-align: center;
    font-family: "Saira Condensed", sans-serif; font-weight: 700;
    font-size: 46px; letter-spacing: 4px; color: #fff; word-spacing: 6px;
  }
  .net-weight {
    position: absolute; left: 0; width: 100%; top: 672px; text-align: center;
    font-family: "Open Sans", sans-serif; font-weight: 500; font-size: 19px; color: #fff;
  }
</style>
</head>
<body>
  <main class="label">
    <div class="check-band" role="img" aria-label="Band of light blue checkered squares"></div>

    <div class="servings-tab">
      <span class="servings-count">40</span>
      <span class="servings-word">servings</span>
    </div>

    <div class="brand">
      <span class="brand-square"></span>
      <h1 class="brand-name">BOUNDLESS VOLT</h1>
    </div>

    <p class="audience">FOR E-SPORT GAMERS</p>

    <svg class="bottom-band" viewBox="0 0 1040 320" aria-hidden="true">
      <rect x="0" y="0" width="1040" height="320" fill="var(--royal-deep)"/>
      <polygon points="490,0 590,0 570,90 470,90" fill="var(--label-white)"/>
      <polygon points="0,0 1040,0 1040,0 0,0" fill="var(--royal)"/>
      <polygon points="130,18 206,18 192,88 116,88" fill="var(--royal)"/>
      <polygon points="218,18 294,18 280,88 204,88" fill="var(--royal)"/>
      <polygon points="306,18 382,18 368,88 292,88" fill="var(--royal)"/>
      <line x1="211" y1="14" x2="196" y2="92" stroke="#fff" stroke-width="4"/>
      <line x1="299" y1="14" x2="284" y2="92" stroke="#fff" stroke-width="4"/>
    </svg>

    <div class="stat" style="left:128px"><div class="stat-zero">0</div><div class="stat-name">SUGAR</div></div>
    <div class="stat" style="left:216px"><div class="stat-zero">0</div><div class="stat-name">CALORIES</div></div>
    <div class="stat" style="left:304px"><div class="stat-zero">0</div><div class="stat-name">CAFFEINE</div></div>

    <p class="flavor">TUNDRA MIST</p>
    <p class="benefits">ENERGY | FOCUS | REACTION | CLARITY</p>
    <p class="net-weight">Dietary Supplement | Net Weight 12 OZ (118g)</p>
  </main>
</body>
</html>
```